We need a business card design for a new company located in Missouri City, TX, entitled 'BrightPath Chiropractic & Holistic Center'. Our services include restoration of health and vitality, spinal exam, health assessment, dietary & fitness programs, lymphatic & therapeutic massage, detox & remineralize body wraps, far infrared sauna therapy

Industry/Entity Type

Business

Contact Information for Business Card

BrightPath Chiropractic & Holistic Center, Marlene Okafor LMT, 4215 Elm Ridge Rd., Suite 310, Missouri City, TX 77482, 281-555-0193

```html
<!DOCTYPE html>
<html lang="en">
<head>
<meta charset="utf-8">
<title>BrightPath Chiropractic &amp; Holistic Center – Business Card</title>
<link rel="stylesheet" href="https://fonts.googleapis.com/css2?family=Arimo:wght@400&family=Marcellus&display=swap">
<style>
  :root {
    --page-bg: #e9e7e4;
    --card-white: #ffffff;
    --card-black: #000000;
    --brand-blue: #1b5e86;
    --brand-teal: #1a9e8c;
    --brand-gray: #6d6e71;
    --tint-blue: #bccfda;
    --tint-teal: #b6e2dc;
    --shade-blue: #0a1c26;
    --shade-teal: #08302b;
    --ink: #111111;
    --white: #ffffff;
  }
  * { box-sizing: border-box; margin: 0; padding: 0; }
  html, body {
    width: 1189px; height: 1200px; overflow: hidden;
    background: var(--page-bg);
  }
  .card {
    position: absolute; left: 136px; width: 916px;
    overflow: hidden;
    box-shadow: 0 6px 14px rgba(0,0,0,.25);
  }
  .card--front { top: 50px; height: 524px; background: var(--card-white); }
  .card--back  { top: 629px; height: 522px; background: var(--card-black); }

  .backdrop-shape { position: absolute; border-radius: 50%; }
  .backdrop-shape--tint-blue { left: 40px; top: 10px; width: 290px; height: 290px; background: var(--tint-blue); }
  .backdrop-shape--tint-teal { left: 38px; top: 270px; width: 250px; height: 250px; background: var(--tint-teal); }
  .backdrop-shape--shade-blue { left: 600px; top: 15px; width: 280px; height: 280px; background: var(--shade-blue); }
  .backdrop-shape--shade-teal { left: 650px; top: 260px; width: 240px; height: 240px; background: var(--shade-teal); }

  .person-name {
    position: absolute; right: 511px; top: 86px;
    font: 48px/1 "Marcellus", serif; color: var(--ink); white-space: nowrap;
  }
  .person-title {
    position: absolute; right: 511px; top: 146px;
    font: 33px/1 "Arimo", sans-serif; color: var(--ink);
  }
  .contact-list { list-style: none; position: absolute; right: 511px; top: 260px; }
  .contact-item {
    display: flex; align-items: center; justify-content: flex-end;
    height: 43px; white-space: nowrap;
    font: 26px/1 "Arimo", sans-serif; color: var(--ink);
  }
  .contact-icon { width: 24px; height: 24px; margin-left: 24px; flex: none; }

  .divider {
    position: absolute; left: 440px; top: 55px; width: 3px; height: 365px;
    background: var(--brand-teal);
  }

  .brand { position: absolute; left: 460px; width: 456px; top: 150px; text-align: center; }
  .brand-dot {
    width: 44px; height: 44px; border-radius: 50%;
    background: var(--brand-teal); margin: 0 auto 22px;
  }
  .brand-name { font: 50px/1 "Marcellus", serif; color: var(--brand-gray); }
  .brand-tagline { font: 29px/1 "Marcellus", serif; color: var(--brand-gray); margin-top: 10px; }

  .footer-band {
    position: absolute; left: 0; right: 0; bottom: 0;
    background: var(--brand-blue);
    border-top: 4px solid var(--brand-teal);
  }
  .card--front .footer-band { height: 77px; display: flex; align-items: center; justify-content: center; }
  .card--back .footer-band { height: 75px; }
  .address { font: 25px/1 "Arimo", sans-serif; color: var(--white); white-space: nowrap; }

  .services-heading {
    position: absolute; left: 43px; top: 36px;
    font: 46px/1 "Arimo", sans-serif; color: var(--brand-blue);
  }
  .services-list { list-style: none; position: absolute; left: 56px; top: 93px; }
  .service {
    display: flex; align-items: center; height: 48px;
    font: 29px/1 "Arimo", sans-serif; color: var(--white); white-space: nowrap;
  }
  .service::before {
    content: ""; width: 14px; height: 14px; border-radius: 50%;
    background: var(--brand-teal); margin: 0 29px 0 6px; flex: none;
  }
</style>
</head>
<body>
  <section class="card card--front">
    <div class="backdrop-shape backdrop-shape--tint-blue"></div>
    <div class="backdrop-shape backdrop-shape--tint-teal"></div>

    <h1 class="person-name">Priya Sandoval</h1>
    <p class="person-title">Director</p>

    <ul class="contact-list">
      <li class="contact-item">281-555-0193
        <svg class="contact-icon" viewBox="0 0 24 24" aria-hidden="true">
          <rect width="24" height="24" rx="2" fill="#111"/>
          <path d="M5 10c0-3 14-3 14 0v1h-4V9H9v2H5z" fill="#fff"/>
          <rect x="7" y="12" width="10" height="7" rx="1" fill="#fff"/>
          <circle cx="12" cy="15.5" r="1.8" fill="#111"/>
        </svg>
      </li>
      <li class="contact-item">www.brightpath.com
        <svg class="contact-icon" viewBox="0 0 24 24" aria-hidden="true">
          <rect width="24" height="24" rx="2" fill="#111"/>
          <circle cx="12" cy="12" r="7.5" fill="none" stroke="#fff" stroke-width="1.8"/>
          <path d="M4.5 12h15M12 4.5c-3 3-3 12 0 15M12 4.5c3 3 3 12 0 15" fill="none" stroke="#fff" stroke-width="1.4"/>
        </svg>
      </li>
      <li class="contact-item">psandoval@brightpath.com
        <svg class="contact-icon" viewBox="0 0 24 24" aria-hidden="true">
          <rect width="24" height="24" rx="2" fill="#111"/>
          <rect x="4" y="7" width="16" height="11" fill="#fff"/>
          <path d="M4 7l8 6 8-6" fill="none" stroke="#111" stroke-width="1.5"/>
        </svg>
      </li>
    </ul>

    <div class="divider"></div>

    <div class="brand">
      <div class="brand-dot"></div>
      <p class="brand-name">BrightPath</p>
      <p class="brand-tagline">Chiropractic &amp; Holistic Center</p>
    </div>

    <footer class="footer-band">
      <p class="address">Marlene Okafor LMT, 4215 Elm Ridge Rd., Suite 310, Missouri City, TX 77482</p>
    </footer>
  </section>

  <section class="card card--back">
    <div class="backdrop-shape backdrop-shape--shade-blue"></div>
    <div class="backdrop-shape backdrop-shape--shade-teal"></div>

    <h2 class="services-heading">Services :</h2>
    <ul class="services-list">
      <li class="service">Restoration of health and vitality</li>
      <li class="service">Spinal exam</li>
      <li class="service">Health assessment</li>
      <li class="service">Dietary &amp; fitness programs</li>
      <li class="service">Lymphatic &amp; therapeutic massage</li>
      <li class="service">Detox &amp; remineralize body wraps</li>
      <li class="service">Far infrared sauna therapy</li>
    </ul>
    <div class="footer-band"></div>
  </section>
</body>
</html>
```